Sierra Lantern Roots Festival Music Conference & Concert Series needs a banner design to welco...

We are looking for a banner to use as a backdrop where people can take pictures and promote the event as they upload to social media. The music conference primarily targets high school students so we are looking for a design that will attract a younger audience. The festival revolves around music appreciation in the US/Mexico border. We like the "Sierra LanternRoots Festival" trumpet logo on the "5th annual" design attached, but we are open to other designs.
Target Market(s)
ages 15-45
Colors
Designer to choose colors to be used in the design.
Look and feel

```html
<!DOCTYPE html>
<html lang="en">
<head>
<meta charset="UTF-8">
<title>Sierra Lantern Roots Festival</title>
<link href="https://fonts.googleapis.com/css2?family=Poppins:wght@700;800&family=Dancing+Script:wght@500&display=swap" rel="stylesheet">
<style>
  :root {
    --violet: #6a2ad8;
    --violet-light: #b98cf0;
    --magenta: #c42ad6;
    --pink-glow: #f070f0;
    --indigo: #33148e;
    --navy: #12084a;
    --ring: rgba(190, 170, 240, 0.62);
    --disc-top: #6e1a22;
    --disc-red: #c4102e;
    --disc-pink: #ee1a6a;
    --disc-orange: #e8541c;
    --white: #ffffff;
  }
  html, body {
    margin: 0;
    padding: 0;
    width: 960px;
    height: 1200px;
    overflow: hidden;
    background: var(--navy);
  }
  .banner {
    position: relative;
    width: 960px;
    height: 1200px;
    overflow: hidden;
  }
  .crowd-scene {
    position: absolute;
    inset: 0;
    background:
      radial-gradient(ellipse 22% 14% at 92% 14%, rgba(255, 190, 255, 0.75), transparent 70%),
      radial-gradient(ellipse 18% 10% at 86% 48%, rgba(240, 110, 230, 0.55), transparent 70%),
      radial-gradient(ellipse 30% 22% at 20% 10%, rgba(190, 170, 250, 0.55), transparent 70%),
      radial-gradient(ellipse 55% 30% at 50% 38%, rgba(120, 60, 230, 0.5), transparent 75%),
      linear-gradient(180deg, var(--violet) 0%, var(--magenta) 20%, #7a28d8 36%, var(--indigo) 60%, var(--navy) 84%);
  }
  .stage-light {
    position: absolute;
    inset: 0;
    width: 960px;
    height: 1200px;
  }
  .artwork {
    position: absolute;
    inset: 0;
    width: 960px;
    height: 1200px;
  }
  .title-edition {
    font-family: "Poppins", sans-serif;
    font-weight: 700;
    font-size: 66px;
    fill: none;
    stroke: var(--white);
    stroke-width: 2.4;
  }
  .title-name {
    font-family: "Poppins", sans-serif;
    font-weight: 800;
    font-size: 106px;
    fill: var(--white);
  }
  .title-kind {
    font-family: "Dancing Script", cursive;
    font-weight: 500;
    font-size: 150px;
    fill: var(--white);
  }
</style>
</head>
<body>
  <main class="banner">
    <div class="crowd-scene" role="img" aria-label="Concert crowd with raised hands under purple stage lights, an acoustic guitar and floating music notes"></div>

    <svg class="stage-light" viewBox="0 0 960 1200" aria-hidden="true">
      <defs>
        <filter id="soft" x="-50%" y="-50%" width="200%" height="200%">
          <feGaussianBlur stdDeviation="18"/>
        </filter>
        <linearGradient id="beam" x1="0" y1="0" x2="0" y2="1">
          <stop offset="0" stop-color="var(--violet-light)" stop-opacity="0.55"/>
          <stop offset="1" stop-color="var(--violet-light)" stop-opacity="0"/>
        </linearGradient>
      </defs>
      <g filter="url(#soft)">
        <polygon points="150,0 230,0 260,430 170,430" fill="url(#beam)"/>
        <polygon points="560,0 640,0 700,460 600,460" fill="url(#beam)"/>
        <polygon points="30,0 90,0 80,330 20,330" fill="url(#beam)" opacity="0.7"/>
        <polygon points="330,0 380,0 400,300 340,300" fill="url(#beam)" opacity="0.6"/>
        <ellipse cx="600" cy="480" rx="120" ry="40" fill="var(--pink-glow)" opacity="0.35"/>
      </g>
    </svg>

    <svg class="artwork" viewBox="0 0 960 1200">
      <defs>
        <linearGradient id="disc-fill" x1="0" y1="0" x2="0" y2="1">
          <stop offset="0" stop-color="var(--disc-top)"/>
          <stop offset="0.3" stop-color="var(--disc-red)"/>
          <stop offset="0.6" stop-color="var(--disc-pink)"/>
          <stop offset="1" stop-color="var(--disc-orange)"/>
        </linearGradient>
      </defs>
      <circle class="emblem-ring" cx="494" cy="707" r="343" fill="var(--ring)"/>
      <circle class="emblem-disc" cx="494" cy="707" r="315" fill="url(#disc-fill)" role="img" aria-label="Acoustic guitar over a warm red glow"/>

      <text class="title-edition" x="491" y="600" text-anchor="middle" textLength="386" lengthAdjust="spacingAndGlyphs">6TH ANNUAL</text>
      <text class="title-name" x="487" y="718" text-anchor="middle" textLength="880" lengthAdjust="spacingAndGlyphs">SIERRA LANTERN</text>
      <text class="title-kind" x="509" y="846" text-anchor="middle" textLength="620" lengthAdjust="spacingAndGlyphs">Roots Festival</text>
    </svg>
  </main>
</body>
</html>
```